Gobal construction supply company needs new business card design

I need a business card design for my global supply company using an existing logo. i will be looking to print these on rounded corner cards with the black background version of my logo on the back. on the front white background, my logo again and my simple details.

```html
<!DOCTYPE html>
<html lang="en">
<head>
<meta charset="UTF-8">
<title>Northgate Supply Works – Business Card</title>
<link rel="stylesheet" href="https://fonts.googleapis.com/css2?family=Oswald:wght@600&family=Work+Sans:wght@400;500;600&display=swap">
<style>
  :root {
    --backdrop: #141414;
    --card-dark: #1b1b1b;
    --card-dark-edge: #262626;
    --card-light: #ffffff;
    --brand-grey: #c4c4c4;
    --ink: #161616;
    --ink-soft: #555555;
    --ink-mid: #333333;
    --divider: #8a8a8a;
  }
  * { margin: 0; padding: 0; box-sizing: border-box; }
  html, body {
    width: 1200px;
    height: 900px;
    overflow: hidden;
    background: var(--backdrop);
  }
  .canvas {
    width: 1200px;
    height: 900px;
    display: flex;
    flex-direction: column;
    align-items: center;
    justify-content: center;
    gap: 40px;
  }
  .card {
    position: relative;
    width: 560px;
    height: 320px;
    border-radius: 14px;
    box-shadow: 0 10px 30px rgba(0,0,0,.5);
    overflow: hidden;
  }

  /* Back: brand on black */
  .card--brand {
    background: linear-gradient(135deg, var(--card-dark) 0%, var(--card-dark-edge) 100%);
    display: flex;
    align-items: center;
    justify-content: center;
  }
  .brand {
    display: flex;
    align-items: center;
    gap: 12px;
  }
  .brand__name {
    font-family: "Work Sans", sans-serif;
    font-weight: 600;
    font-size: 26px;
    letter-spacing: 1px;
    text-transform: uppercase;
    color: var(--brand-grey);
  }
  .brand__dot {
    width: 14px;
    height: 14px;
    border-radius: 50%;
    background: var(--brand-grey);
  }

  /* Front: details on white */
  .card--details { background: var(--card-light); }
  .person {
    position: absolute;
    left: 0;
    top: 110px;
    width: 262px;
    text-align: right;
  }
  .person__name {
    font-family: "Oswald", sans-serif;
    font-weight: 600;
    font-size: 32px;
    line-height: 1;
    text-transform: uppercase;
    color: var(--ink);
  }
  .person__role {
    font-family: "Work Sans", sans-serif;
    font-size: 14px;
    font-weight: 500;
    color: var(--ink-soft);
    margin-top: 4px;
  }
  .divider {
    position: absolute;
    left: 290px;
    top: 110px;
    width: 2px;
    height: 62px;
    background: var(--divider);
  }
  .contacts {
    position: absolute;
    left: 312px;
    top: 108px;
    list-style: none;
    font-family: "Work Sans", sans-serif;
    font-size: 15px;
    color: var(--ink-mid);
    letter-spacing: .5px;
  }
  .contacts li {
    display: flex;
    align-items: center;
    gap: 9px;
    height: 22px;
  }
  .contacts svg { width: 11px; height: 11px; flex: none; }
  .address {
    position: absolute;
    left: 36px;
    bottom: 46px;
    font-family: "Work Sans", sans-serif;
    font-size: 15px;
    letter-spacing: .5px;
    color: var(--ink-mid);
  }
</style>
</head>
<body>
<main class="canvas">
  <section class="card card--brand" aria-label="Card back">
    <div class="brand">
      <span class="brand__name">Northgate Supply Works</span>
      <span class="brand__dot"></span>
    </div>
  </section>

  <section class="card card--details" aria-label="Card front">
    <div class="person">
      <p class="person__name">Daniel Reyes</p>
      <p class="person__role">Director</p>
    </div>
    <div class="divider"></div>
    <ul class="contacts">
      <li>
        <svg viewBox="0 0 12 12" fill="none" stroke="#333333" stroke-width="1.3"><path d="M2.5 1.5h2l1 2.5-1.3 1a6 6 0 0 0 2.8 2.8l1-1.3 2.5 1v2c0 .6-.4 1-1 1A9 9 0 0 1 1.5 2.5c0-.6.4-1 1-1z"/></svg>
        555-014-2286
      </li>
      <li>
        <svg viewBox="0 0 12 12" fill="none" stroke="#333333" stroke-width="1.2"><rect x="1" y="2.5" width="10" height="7" rx="1"/><path d="M1.3 3l4.7 3.5L10.7 3"/></svg>
        info@northgatesupply.com
      </li>
      <li>
        <svg viewBox="0 0 12 12" fill="none" stroke="#333333" stroke-width="1.1"><circle cx="6" cy="6" r="5"/><ellipse cx="6" cy="6" rx="2.2" ry="5"/><path d="M1 6h10"/></svg>
        www.northgatesupply.com
      </li>
    </ul>
    <p class="address">48 Harbor Road Box 902, Cedar Bend, AB</p>
  </section>
</main>
</body>
</html>
```